I need a flyer made , the flyer can be one page or two pages or three pages . I will be posting this on Instagram and social media platforms. I am a luxury home builder , I am looking to hire a construction project manager . Below are some examples and ideas what can be on the flyer

We’re looking for a construction project manager who’s passionate about building luxury homes at the highest standards
We’re hiring construction project manager
* Experience 5+ years in residential project management with a strong portfolio of completed homes.
* location : Bergen County NJ
* excellent leadership skills, leads teams with confidence and clarity
* communicates seamlessly with architects , engineers, designers and clients
*knows how to manage budgets and timelines without compromising quality
*solves problems with a positive solution first mindset
* pays attention to every detail because in luxury the small things are the big things

Apply now , link in bio or DM to connect.

My logo is attached, my web site www.velstridebuilders.com
My style is modern but still warm and inviting. I like a clean classy look .

Please don’t add any images of chairs or people to the flyer , I do not want people on my flyer. Do not add standard images of offices and houses , we are luxury builders , we build homes over 2 million dollars. Keep a classy , simple modern look . High end .

You can add a white hard hat with my logo on it for a image , this is a suggestion does not have to be on my flyer ,

```html
<!DOCTYPE html>
<html lang="en">
<head>
<meta charset="utf-8">
<title>Velstride Builders – Construction Project Manager</title>
<link rel="stylesheet" href="https://fonts.googleapis.com/css2?family=Montserrat:ital,wght@0,400;0,500;0,600;0,700;0,800;1,500;1,700&display=swap">
<style>
  :root {
    --ink: #121212;
    --slate: #a3a8b9;
    --slate-light: #c6c9d4;
    --gold: #7b6843;
    --gold-deep: #6b5a3b;
    --white: #ffffff;
    --text-dark: #1d1d1f;
    --rule: #7d8293;
  }
  * { margin: 0; padding: 0; box-sizing: border-box; }
  html, body { width: 1200px; height: 1200px; overflow: hidden; background: var(--ink); }
  body { font-family: "Montserrat", Arial, sans-serif; }
  .flyer { position: relative; width: 1200px; height: 1200px; background: var(--ink); overflow: hidden; }
  .abs { position: absolute; white-space: nowrap; }

  .eyebrow { left: 84px; top: 58px; font-size: 40px; font-weight: 800; letter-spacing: 12px; color: var(--gold); }
  .headline { left: 74px; top: 96px; font-size: 206px; font-weight: 700; letter-spacing: -4px; color: var(--slate); line-height: 1; }
  .role-kicker { left: 84px; top: 310px; font-size: 37px; font-weight: 600; letter-spacing: 6px; color: var(--slate-light); }
  .role-title { left: 82px; top: 352px; font-size: 64px; font-weight: 700; color: var(--gold); letter-spacing: -0.5px; }

  .exp-num { left: 82px; top: 456px; font-size: 76px; font-weight: 800; color: var(--slate-light); line-height: 1; letter-spacing: -2px; }
  .exp-years { left: 178px; top: 465px; font-size: 35px; font-weight: 800; color: var(--slate-light); line-height: 1; }
  .exp-word { left: 184px; top: 500px; font-size: 20px; font-weight: 600; color: var(--slate-light); }
  .exp-detail { left: 327px; top: 465px; font-size: 27px; font-weight: 700; color: var(--slate-light); line-height: 1.05; }

  .portfolio-pill { left: 83px; top: 544px; width: 560px; height: 40px; background: var(--gold-deep); border-radius: 4px 20px 20px 4px; color: var(--white); font-size: 22px; font-weight: 500; line-height: 40px; padding-left: 19px; letter-spacing: 0.3px; }

  .panel { left: 0; top: 620px; }
  .qualities { position: absolute; left: 0; top: 0; }
  .quality { position: absolute; left: 88px; }
  .quality-icon { position: absolute; left: 0; top: 10px; }
  .quality-title { position: absolute; left: 34px; top: 0; font-size: 22px; font-weight: 800; color: var(--gold); white-space: nowrap; }
  .quality-text { position: absolute; left: 34px; top: 28px; font-size: 18.5px; font-weight: 500; color: var(--text-dark); white-space: nowrap; }
  .quality-rule { position: absolute; left: 34px; top: 58px; height: 1px; background: var(--rule); }

  .brand { left: 780px; top: 62px; width: 380px; text-align: center; color: var(--white); font-weight: 500; }
  .brand-name { font-size: 54px; letter-spacing: 3px; line-height: 1; }
  .brand-sub { font-size: 17px; letter-spacing: 4px; margin-top: 22px; }

  .photo { left: 720px; top: 196px; }

  .location-band { left: 690px; top: 847px; }
  .location-label { right: 77px; top: 862px; font-size: 26px; font-weight: 500; letter-spacing: 4px; color: var(--white); }
  .location-name { right: 72px; top: 895px; font-size: 40px; font-weight: 700; color: var(--white); }

  .apply { left: 752px; top: 962px; font-size: 70px; font-weight: 700; color: var(--slate); letter-spacing: -0.5px; }
  .apply-note { left: 752px; top: 1053px; font-size: 24.5px; font-weight: 500; color: var(--gold); letter-spacing: 0.4px; }
  .social { left: 752px; top: 1104px; display: flex; align-items: center; gap: 14px; }
  .social-dot { width: 36px; height: 36px; border-radius: 50%; background: var(--gold); }
  .social-handle { font-size: 28px; font-weight: 600; color: var(--slate-light); }

  .tagline { left: 84px; top: 1062px; font-size: 26px; font-style: italic; font-weight: 500; letter-spacing: 2.5px; color: var(--slate-light); }
  .tagline strong { color: var(--gold); font-weight: 700; }
  .website { left: 84px; top: 1106px; font-size: 32.5px; font-weight: 700; color: var(--slate-light); }
  .website .accent { color: var(--gold); }
</style>
</head>
<body>
<main class="flyer">

  <div class="abs eyebrow">WE’RE</div>
  <h1 class="abs headline">Hiring</h1>
  <div class="abs role-kicker">CONSTRUCTION</div>
  <h2 class="abs role-title">Project Manager</h2>

  <div class="abs exp-num">5+</div>
  <div class="abs exp-years">YEARS</div>
  <div class="abs exp-word">Experience</div>
  <div class="abs exp-detail">in Residential Project<br>Management</div>
  <div class="abs portfolio-pill">with a strong portfolio of completed homes</div>

  <div class="abs brand">
    <div class="brand-name">VELSTRIDE</div>
    <div class="brand-sub">builders</div>
  </div>

  <svg class="abs photo" width="480" height="652" viewBox="0 0 480 652" role="img" aria-label="Photo of a smiling project manager in a grey suit holding a yellow hard hat and rolled plans">
    <defs>
      <linearGradient id="photoTone" x1="0" y1="0" x2="0" y2="1">
        <stop offset="0" stop-color="#1a1a1a"/>
        <stop offset="0.45" stop-color="#6f7278"/>
        <stop offset="1" stop-color="#9a9ca2"/>
      </linearGradient>
    </defs>
    <path d="M150 0 H330 L440 200 L460 652 H30 L20 300 Z" fill="url(#photoTone)" opacity="0.85"/>
  </svg>

  <svg class="abs panel" width="760" height="440" viewBox="0 0 760 440">
    <path d="M0 0 H730 L664 405 Q658 425 640 425 H0 Z" fill="var(--slate)"/>
    <g fill="none" stroke="var(--rule)" stroke-width="1">
      <line x1="122" y1="111" x2="717" y2="111"/>
      <line x1="122" y1="185" x2="705" y2="185"/>
      <line x1="122" y1="258" x2="693" y2="258"/>
      <line x1="122" y1="332" x2="681" y2="332"/>
    </g>
  </svg>

  <ul class="abs qualities" style="list-style:none; left:0; top:620px;">
    <li class="quality" style="top:44px;">
      <svg class="quality-icon" width="22" height="22" viewBox="0 0 22 22"><circle cx="11" cy="11" r="9.5" fill="none" stroke="#1d1d1f" stroke-width="1.6"/><path d="M6.5 11.2l3 3 6-6" fill="none" stroke="#1d1d1f" stroke-width="1.6"/></svg>
      <span class="quality-title">Excellent leadership skills</span>
      <span class="quality-text">leads teams with confidence and clarity</span>
    </li>
    <li class="quality" style="top:118px;">
      <svg class="quality-icon" width="22" height="22" viewBox="0 0 22 22"><circle cx="11" cy="11" r="9.5" fill="none" stroke="#1d1d1f" stroke-width="1.6"/><path d="M6.5 11.2l3 3 6-6" fill="none" stroke="#1d1d1f" stroke-width="1.6"/></svg>
      <span class="quality-title">Communicates seamlessly</span>
      <span class="quality-text">with architects, engineers, designers and clients</span>
    </li>
    <li class="quality" style="top:192px;">
      <svg class="quality-icon" width="22" height="22" viewBox="0 0 22 22"><circle cx="11" cy="11" r="9.5" fill="none" stroke="#1d1d1f" stroke-width="1.6"/><path d="M6.5 11.2l3 3 6-6" fill="none" stroke="#1d1d1f" stroke-width="1.6"/></svg>
      <span class="quality-title">Knows how to manage</span>
      <span class="quality-text">budgets and timelines without compromising quality</span>
    </li>
    <li class="quality" style="top:266px;">
      <svg class="quality-icon" width="22" height="22" viewBox="0 0 22 22"><circle cx="11" cy="11" r="9.5" fill="none" stroke="#1d1d1f" stroke-width="1.6"/><path d="M6.5 11.2l3 3 6-6" fill="none" stroke="#1d1d1f" stroke-width="1.6"/></svg>
      <span class="quality-title">Solves problems</span>
      <span class="quality-text">with a positive solution first mindset</span>
    </li>
    <li class="quality" style="top:340px;">
      <svg class="quality-icon" width="22" height="22" viewBox="0 0 22 22"><circle cx="11" cy="11" r="9.5" fill="none" stroke="#1d1d1f" stroke-width="1.6"/><path d="M6.5 11.2l3 3 6-6" fill="none" stroke="#1d1d1f" stroke-width="1.6"/></svg>
      <span class="quality-title">Pays attention to every detail</span>
      <span class="quality-text">because in luxury the small things are the big things</span>
    </li>
  </ul>

  <svg class="abs location-band" width="510" height="109" viewBox="0 0 510 109">
    <path d="M28 0 H510 V109 H12 Q0 109 2 97 Z" fill="var(--gold-deep)"/>
  </svg>
  <div class="abs location-label">LOCATION</div>
  <div class="abs location-name">Bergen County, NJ</div>

  <div class="abs apply">Apply Now</div>
  <div class="abs apply-note">Link in Bio or DM to connect.</div>
  <div class="abs social">
    <span class="social-dot"></span>
    <span class="social-handle">velstridebuilders</span>
  </div>

  <div class="abs tagline">Build <strong>Luxury.</strong> Lead <strong>Excellence.</strong></div>
  <div class="abs website"><span class="accent">www.</span>velstridebuilders<span class="accent">.com</span></div>

</main>
</body>
</html>
```